The Brandwell Firm

We need a new design for our letterhead and envelopes. We are a personal injury and criminal defense firm so we need something modern and clean, but more on the professional/traditional side. Our new logo has two colors and is attached to the file so we need something that works well with those colors/matches the design. The following information needs to be on the letterhead:
Phone: (555) 214-3370
Fax: (555) 214-5186
Toll-Free: (888) 431-2059
Post Office Box 4721
Millbrook, SC 29555-4721
HarmClaimCounsel.example
PalmettoTrialAdvocates.example

Target Market(s)

Clients, government agencies, other law firms

Industry/Entity Type

Legal

Font styles to use
Sans Serif
Other font styles liked:
• Arial

Colors

Designer to choose colors to be used in the design.

Requirements
Must have
• Must look professional and clean, modern
Nice to have
• I would like to see a design that works with the logo but does not distract from the content that will be printed on it
Should not have
• Too many colors or crazy designs.

```html
<!DOCTYPE html>
<html lang="en">
<head>
<meta charset="utf-8">
<title>The Brandwell Firm – Stationery</title>
<link href="https://fonts.googleapis.com/css2?family=Roboto:wght@400;500&display=swap" rel="stylesheet">
<style>
  :root {
    --backdrop: #6b6b6b;
    --paper: #f0f0f0;
    --navy: #2a1a6e;
    --red: #c0241f;
    --ink: #6a6a6a;
    --ink-dark: #555555;
    --white: #ffffff;
  }
  * { margin: 0; padding: 0; box-sizing: border-box; }
  html, body { width: 1200px; height: 837px; overflow: hidden; background: var(--backdrop); }
  body { position: relative; font-family: "Roboto", Arial, sans-serif; color: var(--ink); }

  .sheet { position: absolute; background: var(--paper); overflow: hidden; box-shadow: 0 0 0 1px rgba(0,0,0,0.08); }
  .letterhead { left: 115px; top: 122px; width: 417px; height: 590px; }
  .envelope-front { left: 579px; top: 178px; width: 505px; height: 227px; }
  .envelope-back { left: 579px; top: 430px; width: 505px; height: 227px; }

  .brand { position: absolute; display: flex; align-items: center; gap: 6px; }
  .brand-dot { width: 12px; height: 12px; border-radius: 50%; background: var(--red); }
  .brand-name { font-size: 15px; font-weight: 500; color: var(--navy); letter-spacing: 0.2px; }
  .letterhead .brand { left: 26px; top: 50px; }
  .envelope-front .brand { left: 29px; top: 60px; }

  .letter-body { position: absolute; left: 26px; top: 125px; width: 365px; font-size: 6.4px; line-height: 9.6px; }
  .letter-date { margin-bottom: 21px; }
  .recipient { margin-bottom: 18px; }
  .recipient strong { font-weight: 500; color: var(--ink-dark); }
  .salutation { margin-bottom: 9px; }
  .letter-body p.copy { text-align: justify; margin-bottom: 9.6px; }

  .signer { position: absolute; left: 26px; top: 447px; font-size: 6.6px; }
  .signer-name { font-weight: 500; color: var(--ink-dark); }
  .signature { display: block; width: 96px; height: 16px; margin: 5px 0 6px -8px; border-radius: 3px;
    background: linear-gradient(90deg, rgba(42,26,110,0.15), rgba(42,26,110,0.05)); }

  .wave { position: absolute; left: 0; display: block; }
  .letterhead .wave { top: 500px; width: 417px; height: 90px; }
  .envelope-front .wave { top: 142px; width: 505px; height: 85px; }

  .contact { position: absolute; list-style: none; font-size: 6.3px; line-height: 7.6px; color: var(--white); text-align: right; white-space: nowrap; }
  .contact li { display: flex; justify-content: flex-end; align-items: center; gap: 5px; }
  .contact svg { width: 5px; height: 5px; fill: var(--white); flex: none; }
  .letterhead .contact { right: 22px; top: 539px; }
  .envelope-front .contact { right: 23px; top: 179px; }

  .flap { position: absolute; left: 0; top: 0; width: 505px; height: 82px; }
  .flap-web { position: absolute; left: 0; width: 505px; top: 33px; text-align: center; color: var(--white);
    font-size: 6.2px; line-height: 7.4px; letter-spacing: 1.3px; }
</style>
</head>
<body>

<svg width="0" height="0" style="position:absolute">
  <symbol id="i-phone" viewBox="0 0 10 10"><path d="M2 0h2l1 3-1.5 1a6 6 0 0 0 2.5 2.5L7 5l3 1v2a2 2 0 0 1-2 2A8 8 0 0 1 0 2a2 2 0 0 1 2-2z"/></symbol>
  <symbol id="i-fax" viewBox="0 0 10 10"><path d="M2 0h6v3H2zM0 4h10v5H8V7H2v2H0zM3 8h4v2H3z"/></symbol>
  <symbol id="i-pin" viewBox="0 0 10 10"><path d="M5 0a3.6 3.6 0 0 1 3.6 3.6C8.6 6.4 5 10 5 10S1.4 6.4 1.4 3.6A3.6 3.6 0 0 1 5 0zm0 2.2a1.4 1.4 0 1 0 0 2.8 1.4 1.4 0 0 0 0-2.8z"/></symbol>
  <symbol id="i-web" viewBox="0 0 10 10"><circle cx="5" cy="5" r="4.5"/></symbol>
</svg>

<section class="sheet letterhead">
  <div class="brand"><span class="brand-dot"></span><span class="brand-name">The Brandwell Firm</span></div>

  <div class="letter-body">
    <p class="letter-date">30/20/2016</p>
    <p class="recipient"><strong>Mr. XYZ Smith</strong><br>123, Street No. 123,<br>City Name<br>Pincode-123456</p>
    <p class="salutation">Dear Sir,</p>
    <p class="copy">Lorem Ipsum is simply dummy text of the printing and typesetting industry. Lorem Ipsum has been the industry's standard dummy text ever since the 1500s, when an unknown printer took a galley of type and scrambled it to make a type specimen book. It has survived not only five centuries, but also the leap into electronic typesetting, remaining essentially unchanged. It was popularised in the 1960s with the release of Typeleaf sheets containing Lorem Ipsum passages, and more recently with desktop publishing software like Quillset Layout including versions of Lorem Ipsum.</p>
    <p class="copy">Lorem Ipsum is simply dummy text of the printing and typesetting industry. Lorem Ipsum has been the industry's standard dummy text ever since the 1500s, when an unknown printer took a galley of type and scrambled it to make a type specimen book. It has survived not only five centuries, but also the leap into electronic typesetting, remaining essentially unchanged. It was popularised in the 1960s with the release of Typeleaf sheets containing Lorem Ipsum passages, and more recently with desktop publishing software like Quillset Layout including versions of Lorem Ipsum.</p>
    <p class="copy">Lorem Ipsum is simply dummy text of the printing and typesetting industry. Lorem Ipsum has been the industry's standard dummy text ever since the 1500s, when an unknown printer took a galley of type and scrambled it to make a type specimen book.</p>
    <p class="copy">Lorem Ipsum is simply dummy text of the printing and typesetting industry. Lorem Ipsum has been the industry's standard dummy text ever since the 1500s, when an unknown printer took a galley of type and scrambled it to make a type specimen book.</p>
  </div>

  <div class="signer">
    <p class="signer-name">Your Name</p>
    <span class="signature" role="img" aria-label="Handwritten signature"></span>
    <p>CEO &nbsp;|&nbsp; Owner</p>
  </div>

  <svg class="wave" viewBox="0 0 417 90" preserveAspectRatio="none" aria-hidden="true">
    <path fill="var(--red)" d="M0,54 C90,58 160,56 225,42 C300,22 370,8 417,2 L417,9 C370,15 300,29 228,50 C160,64 90,66 0,62 Z"/>
    <path fill="var(--navy)" d="M0,84 C90,86 160,76 230,58 C300,38 370,22 417,16 L417,90 L0,90 Z"/>
    <path fill="var(--red)" d="M0,70 C60,74 130,78 195,74 C130,84 60,82 0,78 Z"/>
  </svg>

  <ul class="contact">
    <li>(555) 214-3370 <svg><use href="#i-phone"/></svg></li>
    <li>(555) 214-5186 <svg><use href="#i-fax"/></svg></li>
    <li>(888) 431-2059 <svg><use href="#i-phone"/></svg></li>
    <li>Post Office Box 4721 Millbrook, SC 29555-4721 <svg><use href="#i-pin"/></svg></li>
    <li>HarmClaimCounsel.example, PalmettoTrialAdvocates.example <svg><use href="#i-web"/></svg></li>
  </ul>
</section>

<section class="sheet envelope-front">
  <div class="brand"><span class="brand-dot"></span><span class="brand-name">The Brandwell Firm</span></div>

  <svg class="wave" viewBox="0 0 505 85" preserveAspectRatio="none" aria-hidden="true">
    <path fill="var(--red)" d="M0,60 C120,70 220,82 330,42 C400,16 460,4 505,0 L505,8 C460,12 400,24 335,50 C220,92 120,76 0,68 Z"/>
    <path fill="var(--navy)" d="M0,80 C120,86 230,86 350,46 C410,26 465,14 505,12 L505,85 L0,85 Z"/>
    <path fill="var(--red)" d="M0,56 C90,60 180,66 265,60 C180,72 90,72 0,66 Z"/>
  </svg>

  <ul class="contact">
    <li>(555) 214-3370 <svg><use href="#i-phone"/></svg></li>
    <li>(555) 214-5186 <svg><use href="#i-fax"/></svg></li>
    <li>(888) 431-2059 <svg><use href="#i-phone"/></svg></li>
    <li>Post Office Box 4721 Millbrook, SC 29555-4721 <svg><use href="#i-pin"/></svg></li>
  </ul>
</section>

<section class="sheet envelope-back">
  <svg class="flap" viewBox="0 0 505 82" aria-hidden="true">
    <path fill="var(--red)" d="M0,0 L505,0 L478,60 Q469,81 447,81 L58,81 Q36,81 27,60 Z"/>
  </svg>
  <p class="flap-web">harmclaimcounsel.example<br>palmettotrialadvocates.example</p>
</section>

</body>
</html>
```